Carpet cleaning company focused on high quality needs business cards

We are a growing company that just merged with another company and need to design a new business card. We do both residential as well as commercial cleaning. We do carpet, tile & grout, upholstery, hard floors, and stain & pet odor removal. We treat our customers like family and strive to achieve outstanding results with every job.

```html
<!DOCTYPE html>
<html lang="en">
<head>
<meta charset="utf-8">
<title>Brightway Steam Cleaning – Business Cards</title>
<link href="https://fonts.googleapis.com/css2?family=Open+Sans:wght@400;600;800&display=swap" rel="stylesheet">
<style>
  :root {
    --stage: #232323;
    --paper: #ffffff;
    --red: #e8443a;
    --blue: #0a86c8;
    --ink: #161616;
    --muted: #2b2b2b;
  }
  * { box-sizing: border-box; margin: 0; padding: 0; }
  html, body { width: 1200px; height: 780px; overflow: hidden; background: var(--stage); }
  body { font-family: "Open Sans", Arial, sans-serif; color: var(--ink); position: relative; }

  .card {
    position: absolute;
    width: 550px; height: 316px;
    background: var(--paper);
    border-radius: 22px;
    border-bottom: 5px solid var(--red);
    overflow: hidden;
    box-shadow: 0 14px 30px rgba(0,0,0,.55);
  }
  .card--front { left: 35px; top: 232px; }
  .card--back  { left: 615px; top: 232px; }

  /* brand wordmark */
  .brand { display: flex; align-items: center; gap: 12px; }
  .brand__square { width: 34px; height: 34px; background: var(--red); flex: none; }
  .brand__name {
    font-weight: 800; color: var(--ink); line-height: 1.05;
    text-transform: uppercase; letter-spacing: .5px;
  }

  /* front */
  .card--front .brand { position: absolute; left: 0; right: 0; top: 70px; justify-content: center; }
  .card--front .brand__name { font-size: 30px; }
  .services { position: absolute; left: 40px; right: 40px; top: 178px; text-align: center; }
  .services__heading {
    display: flex; align-items: center; gap: 10px;
    color: var(--red); font-weight: 600; font-size: 13px; letter-spacing: .5px;
    margin-bottom: 10px;
  }
  .services__heading::before, .services__heading::after {
    content: ""; flex: 1; height: 1.5px; background: var(--red);
  }
  .services__list { list-style: none; font-size: 12.5px; line-height: 1.75; color: var(--muted); }
  .services__list li { display: inline; margin: 0 5px; }
  .services__list li::before {
    content: ""; display: inline-block; width: 7px; height: 7px; border-radius: 50%;
    background: var(--red); margin-right: 5px; vertical-align: 1px;
  }

  /* back */
  .card--back .brand { position: absolute; left: 30px; top: 30px; }
  .card--back .brand__square { width: 24px; height: 24px; }
  .card--back .brand__name { font-size: 19px; }
  .divider { position: absolute; left: 220px; right: 0; top: 122px; height: 1.5px; background: var(--ink); }
  .person { position: absolute; left: 30px; top: 112px; padding-left: 14px; border-left: 6px solid var(--red); }
  .person__name { font-size: 26px; font-weight: 800; line-height: 1.1; }
  .person__first { color: var(--red); }
  .person__last { color: var(--blue); }
  .person__role { font-size: 14px; color: var(--muted); }
  .contacts { position: absolute; left: 44px; top: 186px; list-style: none; font-size: 13.5px; color: var(--muted); }
  .contacts li { display: flex; align-items: center; gap: 9px; line-height: 24px; }
  .contacts svg { width: 14px; height: 14px; fill: var(--red); flex: none; }
  .address { position: absolute; right: 30px; top: 150px; text-align: right; font-size: 13.5px; line-height: 1.45; color: var(--muted); }
  .bands { position: absolute; left: 0; bottom: 0; width: 550px; height: 70px; }
</style>
</head>
<body>

<section class="card card--front" aria-label="Card front">
  <div class="brand">
    <span class="brand__square"></span>
    <span class="brand__name">Brightway<br>Steam Cleaning</span>
  </div>
  <div class="services">
    <h2 class="services__heading">OUR SERVICES</h2>
    <ul class="services__list">
      <li>Both residential as well as commercial cleaning</li>
      <li>Carpet</li><li>Tile &amp; grout</li><li>Upholstery</li><li>Hard floors</li><li>Stain &amp; pet odor removal</li>
    </ul>
  </div>
</section>

<section class="card card--back" aria-label="Card back">
  <div class="brand">
    <span class="brand__square"></span>
    <span class="brand__name">Brightway<br>Steam Cleaning</span>
  </div>
  <div class="divider"></div>
  <div class="person">
    <p class="person__name"><span class="person__first">Lena</span> <span class="person__last">Marlow</span></p>
    <p class="person__role">Managing Director</p>
  </div>
  <ul class="contacts">
    <li><svg viewBox="0 0 24 24"><path d="M6.6 10.8a15 15 0 0 0 6.6 6.6l2.2-2.2a1 1 0 0 1 1-.25 11.4 11.4 0 0 0 3.6.57 1 1 0 0 1 1 1V20a1 1 0 0 1-1 1A17 17 0 0 1 3 4a1 1 0 0 1 1-1h3.5a1 1 0 0 1 1 1c0 1.25.2 2.45.57 3.57a1 1 0 0 1-.25 1z"/></svg>(555) 014-2290</li>
    <li><svg viewBox="0 0 24 24"><path d="M2 5h20v14H2zm2 2v.5l8 5 8-5V7zm0 2.8V17h16V9.8l-8 5z"/></svg>info@brightwaysteam.com</li>
    <li><svg viewBox="0 0 24 24"><path d="M12 2a10 10 0 1 0 0 20 10 10 0 0 0 0-20zm6.9 6h-3a15 15 0 0 0-1.3-3.9A8 8 0 0 1 18.9 8zM12 4c.8 1.2 1.5 2.5 1.9 4h-3.8c.4-1.5 1.1-2.8 1.9-4zM4.3 14a8 8 0 0 1 0-4h3.4a16 16 0 0 0 0 4zm.8 2h3a15 15 0 0 0 1.3 3.9A8 8 0 0 1 5.1 16zm3-8h-3a8 8 0 0 1 4.3-3.9A15 15 0 0 0 8.1 8zM12 20c-.8-1.2-1.5-2.5-1.9-4h3.8c-.4 1.5-1.1 2.8-1.9 4zm2.3-6H9.7a14 14 0 0 1 0-4h4.6a14 14 0 0 1 0 4zm.3 5.9A15 15 0 0 0 15.9 16h3a8 8 0 0 1-4.3 3.9zm1.7-5.9a16 16 0 0 0 0-4h3.4a8 8 0 0 1 0 4z"/></svg>www.brightwaysteam.com</li>
  </ul>
  <p class="address">418 Linden Ave. Suite<br>120 Riverton, TX 75001</p>
  <svg class="bands" viewBox="0 0 550 70" preserveAspectRatio="none" aria-hidden="true">
    <polygon points="0,70 0,62 430,28 550,0 550,70" fill="var(--red)"/>
    <polygon points="0,70 0,64 330,40 360,40 0,70" fill="var(--paper)"/>
    <polygon points="0,70 0,60 350,42 380,42 240,70" fill="var(--blue)"/>
  </svg>
</section>

</body>
</html>
```